Social Media Graphics - Oakline Push REVISED

Create 6-7 individual social media graphics (square size) to encourage folks to join our online course called:

The Harvest Ledger Circle
How to Launch a Multi-Million Business From Scratch
Sign Up Today!

IMPORTANT: Make the largest and most prominent text on the graphic be: How to Launch a Multi-Million Business From Scratch

For the color scheme of the graphics, let's try a blue color palette; make sure the graphics appeal to both men and women

Make sure each graphic contains 1 of the 3 pics attached (crop pic as needed); and make sure one of the graphics is all TEXT only.

Target Market(s)

men and women looking to start a business

Industry/Entity Type

Entrepreneurship

Colors
0054AA
0677BA
7BADD7
CADEEF
E8F1F8

Requirements
Must have
• All the text and use the 3 pics provided; one graphic can be all text; Simple, modern design that's easy to read

```html
<!DOCTYPE html>
<html lang="en">
<head>
<meta charset="utf-8">
<title>The Harvest Ledger Circle — Sign Up Today</title>
<link rel="stylesheet" href="https://fonts.googleapis.com/css2?family=Anton&family=Oswald:wght@700&display=swap">
<style>
  :root {
    --navy-deep: #053c6a;
    --blue-mid: #0677ba;
    --blue-bright: #0a93d6;
    --panel: #1f1f3d;
    --accent: #1ea2ea;
    --frame: #2fa8f0;
    --white: #ffffff;
  }
  html, body {
    margin: 0;
    padding: 0;
    width: 1200px;
    height: 1200px;
    overflow: hidden;
  }
  .poster {
    position: relative;
    width: 1200px;
    height: 1200px;
    overflow: hidden;
    background:
      radial-gradient(ellipse 700px 520px at 1020px 120px, rgba(12,150,220,0.95), rgba(12,150,220,0) 70%),
      radial-gradient(ellipse 420px 260px at 1150px 720px, rgba(10,140,210,0.55), rgba(10,140,210,0) 70%),
      linear-gradient(135deg, #053a66 0%, #064b80 45%, #0677ba 75%, #0a8ccc 100%);
  }
  .course-title {
    position: absolute;
    left: 0;
    top: 0;
    width: 1200px;
    height: 600px;
  }
  .course-title text {
    font-family: "Anton", "Impact", sans-serif;
    fill: var(--white);
  }
  .hosts-photo {
    position: absolute;
    left: 520px;
    top: 112px;
    width: 640px;
    height: 470px;
    border-radius: 220px 220px 0 0;
    background:
      radial-gradient(ellipse 200px 260px at 230px 250px, rgba(170,170,170,0.55), rgba(170,170,170,0) 75%),
      radial-gradient(ellipse 170px 240px at 500px 260px, rgba(40,70,140,0.6), rgba(40,70,140,0) 75%),
      linear-gradient(180deg, rgba(11,120,190,0) 0%, rgba(20,60,110,0.35) 100%);
  }
  .headline-panel {
    position: absolute;
    left: 57px;
    top: 566px;
    width: 1075px;
    height: 480px;
    background: var(--panel);
    border-radius: 22px;
  }
  .headline-panel .frame {
    position: absolute;
    inset: 14px;
    border: 1.5px solid var(--frame);
    border-radius: 18px;
  }
  .headline-panel .frame-inner {
    position: absolute;
    inset: 19px;
    border: 1.5px solid var(--frame);
    border-radius: 15px;
  }
  .headline {
    position: absolute;
    left: 0;
    top: 0;
    width: 1075px;
    height: 480px;
  }
  .headline text {
    font-family: "Anton", "Impact", sans-serif;
    fill: var(--white);
  }
  .cta {
    position: absolute;
    left: 57px;
    top: 1084px;
    width: 1075px;
    height: 48px;
    display: flex;
    align-items: center;
    gap: 26px;
  }
  .cta .rule {
    flex: 1;
    height: 4px;
    background: var(--accent);
  }
  .cta .label {
    font-family: "Oswald", "Arial Narrow", sans-serif;
    font-weight: 700;
    font-size: 42px;
    letter-spacing: 8px;
    color: var(--accent);
    line-height: 1;
  }
</style>
</head>
<body>
<main class="poster">
  <svg class="course-title" viewBox="0 0 1200 600" aria-label="The Harvest Ledger Circle">
    <text x="100" y="236" font-size="132" textLength="196" lengthAdjust="spacingAndGlyphs">THE</text>
    <text x="100" y="372" font-size="108" textLength="410" lengthAdjust="spacingAndGlyphs">HARVEST</text>
    <text x="96" y="514" font-size="92" textLength="428" lengthAdjust="spacingAndGlyphs">LEDGER CIRCLE</text>
  </svg>

  <div class="hosts-photo" role="img" aria-label="Photo of the two course hosts smiling, one speaking into a microphone"></div>

  <section class="headline-panel">
    <div class="frame"></div>
    <div class="frame-inner"></div>
    <svg class="headline" viewBox="0 0 1075 480" aria-label="How to launch a multi-million business from scratch">
      <text x="76" y="176" font-size="148" textLength="924" lengthAdjust="spacingAndGlyphs">HOW TO LAUNCH</text>
      <text x="76" y="319" font-size="148" textLength="924" lengthAdjust="spacingAndGlyphs">A MULTI-MILLION</text>
      <text x="76" y="425" font-size="98" textLength="926" lengthAdjust="spacingAndGlyphs">BUSINESS FROM SCRATCH</text>
    </svg>
  </section>

  <div class="cta">
    <span class="rule"></span>
    <span class="label">SIGN UP TODAY</span>
    <span class="rule"></span>
  </div>
</main>
</body>
</html>
```